Sell the dream! Property investment proposal document

We are looking for a proposal document which outlines our vision for property development. The purpose of the document is to raise investment from investors - sell the dream!
Brief summary:
Kestrel Dwellings Developments, is an emerging New Zealand property investment company with a focus on providing unique property investment opportunities.
Our expertise and capabilities in architectural modular homes provide us with a remarkable advantage in tackling the development of properties that are typically considered challenging, remote, or uniquely positioned.
Our specialization in this niche sector of property development not only sets us apart from competitors, but also paves the way for lucrative investment opportunities in the New Zealand property market.
Feel free to use any images from www.kestreldwellings.co.nz
Target Market(s)
investors for a unique property development opportunity
Industry/Entity Type
luxury property development in unique locations throughout New Zealand
Colors
Designer to choose only greyscale colors for use in the design.
Look and feel

```html
<!DOCTYPE html>
<html lang="en">
<head>
<meta charset="utf-8">
<title>Kestrel Dwellings Developments – Investment Proposal</title>
<link href="https://fonts.googleapis.com/css2?family=Poppins:wght@300;400;500;700&display=swap" rel="stylesheet">
<style>
:root{
  --stage:#dcdcdc;
  --page:#1f1f1f;
  --page-alt:#1a1a1a;
  --panel:#2e2e2e;
  --white:#ffffff;
  --soft:#d6d6d6;
  --muted:#8a8a8a;
  --frame:#555555;
}
*{margin:0;padding:0;box-sizing:border-box}
html,body{width:1034px;height:1200px;overflow:hidden;background:var(--stage)}
body{position:relative;font-family:'Poppins',sans-serif;color:var(--white)}
.spread{position:absolute;left:51px;width:931px;height:329px;background:var(--page);box-shadow:0 3px 8px rgba(0,0,0,.35);overflow:hidden}
.spread--cover{top:72px}
.spread--overview{top:434px}
.spread--advantage{top:795px}
.abs{position:absolute}
.photo{position:absolute}
.photo--framed{border:1.5px solid var(--frame)}
.texture{position:absolute;background:var(--page-alt)}
.wordmark{position:absolute;font-family:'Poppins',sans-serif;font-weight:300;color:var(--white);letter-spacing:-.5px;line-height:1}
.contact{position:absolute;left:48px;top:235px;font-size:6.6px;line-height:11px;color:var(--soft)}
.contact li{list-style:none;display:flex;align-items:center;gap:5px}
.contact svg{width:6px;height:6px;fill:var(--muted)}
.sell{position:absolute;left:31px;top:135px;font-size:23px;font-weight:300;color:#9a9a9a;line-height:1}
.dream{position:absolute;left:31px;top:160px;font-size:24px;font-weight:700;color:var(--white);line-height:1;white-space:nowrap}
.tagline{position:absolute;left:31px;top:201px;width:150px;font-size:7.4px;font-weight:300;line-height:10.4px;color:var(--soft)}
.site{position:absolute;font-size:5.6px;letter-spacing:1.6px;color:var(--soft);display:flex;align-items:center;gap:6px;white-space:nowrap}
.site--bold{font-size:7px;font-weight:500;letter-spacing:2.4px}
.folio{display:inline-block;background:#555;color:var(--soft);font-size:5px;padding:1px 2px;letter-spacing:0}
.heading{position:absolute;font-size:10px;letter-spacing:3px;font-weight:400;color:var(--white);white-space:nowrap}
.heading b{font-weight:700;color:var(--muted)}
.body{position:absolute;font-size:4.4px;line-height:5.9px;color:var(--soft);font-weight:300}
.body p{margin-bottom:4px}
</style>
</head>
<body>

<!-- Cover spread -->
<section class="spread spread--cover">
  <div class="wordmark" style="left:48px;top:186px;font-size:30px">Kestrel</div>
  <ul class="contact">
    <li><svg viewBox="0 0 10 10"><path d="M2 1l2 0 1 2-1 1c.6 1.2 1.4 2 2.6 2.6l1-1 2 1 0 2c-4 .5-8-3.5-7.6-7.6z"/></svg>09 555 0142</li>
    <li><svg viewBox="0 0 10 10"><rect x="1" y="2" width="8" height="6"/></svg>sales@kestreldwellings.co.nz</li>
    <li><svg viewBox="0 0 10 10"><circle cx="5" cy="5" r="4"/></svg>www.kestreldwellings.co.nz</li>
  </ul>
  <div class="photo" role="img" aria-label="Modern dark timber house on green coastal hills at sunset, with a winding driveway and the sea behind" style="left:233px;top:0;width:465px;height:329px;background:linear-gradient(180deg,#c9b58e 0%,#9a9482 22%,#7d7a6c 32%,#5d6a3a 45%,#4e5a2c 70%,#6b6434 100%)"></div>
  <div class="texture" style="left:698px;top:0;width:233px;height:329px"></div>
  <div class="wordmark" style="left:729px;top:50px;font-size:32px">Kestrel</div>
  <div class="abs" style="left:698px;top:0;width:233px;height:329px">
    <div class="sell">SELL</div>
    <div class="dream">THE DREAM!</div>
    <p class="tagline">Homes Developments, is an emerging New Zealand property investment company</p>
    <div class="site site--bold" style="left:31px;top:270px">www.kestreldwellings.co.nz</div>
  </div>
</section>

<!-- Overview & origins spread -->
<section class="spread spread--overview">
  <h2 class="heading" style="left:48px;top:46px">BUSINESS <b>OVERVIEW</b></h2>
  <div class="body" style="left:48px;top:72px;width:146px">
    <p>Kestrel Dwellings Developments, is an emerging New Zealand property investment company with a focus on providing unique property investment opportunities.</p>
    <p>Our expertise and capabilities in architectural modular homes provide us with a remarkable advantage in tackling the development of properties that are typically considered challenging, remote, or uniquely positioned.</p>
    <p>As a company, with 48 employees boasting a wealth of experience in handling complex architectural projects, making us well-equipped to navigate the intricacies and demands of such ventures.</p>
    <p>This advantage allows us to not only execute projects efficiently but also to deliver exceptional results within condensed time frames.</p>
    <p>By capitalizing on our ability to develop difficult, remote, or one-of-a-kind properties swiftly and effectively, Kestrel Dwellings Developments offers investors a rare chance to engage in projects that promise exceptional profitability in the New Zealand property market.</p>
    <p>Our specialization in this niche sector of property development not only sets us apart from competitors, but also paves the way for lucrative investment opportunities in the New Zealand property market.</p>
  </div>
  <div class="wordmark" style="left:48px;top:261px;font-size:17px">Kestrel</div>
  <div class="abs" style="left:254px;top:0;width:212px;height:329px;background:var(--panel)"></div>
  <div class="photo" role="img" aria-label="Glass-walled cantilevered house on a gravel shore facing a sunset over the sea" style="left:254px;top:0;width:212px;height:257px;background:linear-gradient(180deg,#a9bccb 0%,#c9c9bf 40%,#d9c08a 55%,#6f7272 70%,#7a7168 100%)"></div>
  <div class="site" style="left:289px;top:273px">www.kestreldwellings.co.nz <span class="folio">01</span></div>

  <h2 class="heading" style="left:518px;top:46px">BUSINESS <b>ORIGINS</b></h2>
  <div class="body" style="left:518px;top:72px;width:162px">
    <p>Kestrel Dwellings Developments, is an emerging New Zealand property investment company with a focus on providing unique property investment opportunities.</p>
    <p>Our expertise and capabilities in architectural modular homes provide us with a remarkable advantage in tackling the development of properties that are typically considered challenging, remote, or uniquely positioned.</p>
    <p>As a company, with 48 employees boasting a wealth of experience in handling complex architectural projects, making us well-equipped to navigate the intricacies and demands of such ventures.</p>
    <p>This advantage allows us to not only execute projects efficiently but also to deliver exceptional results within condensed time frames.</p>
    <p>By capitalizing on our ability to develop difficult, remote, or one-of-a-kind properties swiftly and effectively, Kestrel Dwellings Developments offers investors a rare chance to engage in projects that promise exceptional profitability in the New Zealand property market.</p>
    <p>Our specialization in this niche sector of property development not only sets us apart from competitors, but also paves the way for lucrative investment opportunities in the New Zealand property market.</p>
  </div>
  <div class="wordmark" style="left:514px;top:261px;font-size:17px">Kestrel</div>
  <div class="texture" style="left:711px;top:0;width:220px;height:329px"></div>
  <div class="photo photo--framed" role="img" aria-label="Interior with lounge chairs facing a wide window over the ocean" style="left:737px;top:40px;width:145px;height:97px;background:linear-gradient(180deg,#2a2a2a 0%,#7ea6cf 20%,#4f7fae 55%,#2b2b2b 75%,#1a1a1a 100%)"></div>
  <div class="photo photo--framed" role="img" aria-label="Bright living room with floor-to-ceiling glass looking over green hills and a bay" style="left:737px;top:148px;width:145px;height:97px;background:linear-gradient(180deg,#d9d4cc 0%,#a9c3dc 25%,#7d8f78 55%,#c9b59a 80%,#e4ddd2 100%)"></div>
  <div class="site" style="left:755px;top:273px">www.kestreldwellings.co.nz <span class="folio">01</span></div>
</section>

<!-- Advantage & financial spread -->
<section class="spread spread--advantage">
  <div class="texture" style="left:99px;top:0;width:250px;height:25px"></div>
  <div class="photo photo--framed" role="img" aria-label="Dark modern house set in rolling green farmland at golden hour with the sea behind" style="left:50px;top:48px;width:366px;height:110px;background:linear-gradient(180deg,#8e8a7a 0%,#6b6e4a 25%,#4f5a28 55%,#2f3020 80%,#58502a 100%)"></div>
  <h2 class="heading" style="left:48px;top:180px">COMPETITIVE <b>ADVANTAGE</b></h2>
  <div class="body" style="left:48px;top:202px;width:372px">
    <p>Our competitive advantage lies in the uniqueness of our property investment opportunities. Unlike traditional real estate companies, we focus on offering properties that are not only profitable but also aesthetically pleasing and unique. By catering to the tastes of architecture lovers, we set ourselves apart from the competition and attract a niche market of customers who appreciate the artistry and design of our projects.</p>
    <p>Additionally, the streamlined and condensed timelines facilitated by our modular approach provide quicker returns on investment.</p>
  </div>
  <div class="wordmark" style="left:48px;top:257px;font-size:17px">Kestrel</div>
  <div class="site" style="left:289px;top:273px">www.kestreldwellings.co.nz <span class="folio">01</span></div>

  <h2 class="heading" style="left:518px;top:49px">FINANCIAL <b>SUMMARY</b></h2>
  <div class="body" style="left:518px;top:74px;width:154px">
    <p>In terms of financial projections, with each development, we anticipate a profit of 10%-20% which will be project dependent.</p>
    <p>This growth is fueled by the increasing demand for unique property investments in New Zealand and our ability to deliver high-quality services to the market in a condensed time frame, with heavily controlled costs.</p>
    <p>With a solid business model and a dedicated team, we are confident in our ability to achieve success and establish Kestrel Dwellings Investments as a trusted name in the industry.</p>
    <p>New Zealand's property market has been experiencing steady growth over the years, making it an attractive destination for property investors. With its beautiful landscapes and strong economy, New Zealand offers a diverse range of investment opportunities for both local and international investors. The demand for quality properties in prime locations continues to rise, creating a favorable environment for property investment companies like ours that can lean on our modular benefits of being able to reach unique and remote locations.</p>
  </div>
  <div class="wordmark" style="left:514px;top:257px;font-size:17px">Kestrel</div>
  <div class="texture" style="left:711px;top:0;width:220px;height:329px"></div>
  <div class="photo photo--framed" role="img" aria-label="Corner glass room with a leather armchair looking out to misty rocky mountains" style="left:737px;top:40px;width:145px;height:212px;background:linear-gradient(180deg,#2a2724 0%,#9a9386 30%,#b4a78c 55%,#5a5046 80%,#3a3430 100%)"></div>
  <div class="site" style="left:755px;top:273px">www.kestreldwellings.co.nz <span class="folio">01</span></div>
</section>

</body>
</html>
```